Flyer Vacation Gift Certificate

I need to create a beautiful flyer 8.5 x 11 PDF format flyer design. <br/><br/>Instructions:<br/>The flyer will really be a gift voucher for a las vegas vacation getaway. So must have a Las Vegas Theme exciting fun<br/><br/>The voucher should have two modules that will be editable. <br/>Must have a "Compliments Of" area and also must have an "Exclusively For" area<br/><br/>Keep in mind that this flyer will be printed so keep that in mind :)<br/><br/>Here the is the content for the vacation voucher:<br/><br/>There is no doubt that Las Vegas is one of the hottest travel destinations around the world. In fact, some people would even go as far as<br/>saying that perhaps it is THE hottest place to visit. Enjoy up to 4 nights of resort/casino accommodations in exciting Las Vegas, NV. Millions of people travel to this exciting city each year to enjoy its thrills. Thanks to the business you received this certificate from, now you can enjoy exciting Las Vegas, NV too!<br/><br/>Features:<br/>*Travel 7 Days A Week<br/>*Stay Your Choice Of Nights (1-4 Nights)<br/>*Good For Two Adults & Two Children<br/>*Pay Just The Taxes & Fees<br/>*Multiple Travel Date Requests Allowed<br/>*Fully Transferable To Another Person<br/>*Just A 30 Days Advance Notice Required<br/>*You Will Have 12 Months To Complete Travel After Redemption<br/><br/>HOW CAN WE DO THIS?<br/><br/>We contract with the world leading hotel chains and resorts to help them fill their otherwise empty rooms.<br/><br/>We help fill empty rooms which the hotels, resorts and cruise lines turn into additional revenue from other areas of their property and future bookings.<br/><br/>Hotels rarely experience full occupancy, yet they remain open, providing rooms and services at fixed costs. So when hotels give out their rooms by partnering with marketing companies like us, they might miss out on the room fee, but they already didn't have that in the first place, at least now they have the opportunity to gain a customer for their in-house restaurants, room service, their casinos, an extra day stay, future bookings, etc.<br/><br/>VIEW ALL THE DETAILS OF THIS SPECIAL OFFER AND REDEEM ONLINE AT <br/>WWW.QOTAVERNIX.COM<br/><br/>Certificate ID # 47261-38157<br/>Expires 02/29/2020<br/><br/><br/>*terms and conditions apply see website for details<br/><br/>KEEP IN MIND THE EXAMPLES I AM UPLOADING ARE SIMPLY TO SHOW YOU THAT THEY CONTAIN THE "COMPLIMENTS OF" AND "EXCLUSIVELY FOR" ELEMENTS. THESE MUST BE INCLUDED IN NEW DESIGN. PLEASE ONLY USE THE CONTENT I PROVIDED IN BRIEF, DONT USE CONTENT FROM EXAMPLES.

Target Market(s)

CONSUMERS THAT HAVE BEEN REWARDED WITH A VACATION CERTIFICATE FOR DOING BUSINESS WITH A COMPANY.

COMPANIES USE THESE AS MARKETING INCENTIVES TO ATTRACT MORE CUSTOMERS AND TO REWARD LOYALTY, ETC.

Industry/Entity Type

Travel Industry

Colors

Designer to choose colors to be used in the design.

Requirements
Must have
• I need to create a beautiful flyer 8.5 x 11 PDF format flyer design.
• Instructions:
• The flyer will really be a gift voucher for a las vegas vacation getaway. So must have a Las Vegas Theme exciting fun
• The voucher should have two modules that will be editable.
• Must have a "Compliments Of" area and also must have an "Exclusively For" area
• Keep in mind that this flyer will be printed so keep that in mind :)
• Here the is the content for the vacation voucher:
• There is no doubt that Las Vegas is one of the hottest travel destinations around the world. In fact, some people would even go as far as
• saying that perhaps it is THE hottest place to visit. Enjoy up to 4 nights of resort/casino accommodations in exciting Las Vegas, NV. Millions of people travel to this exciting city each year to enjoy its thrills. Thanks to the business you received this certificate from, now you can enjoy exciting Las Vegas, NV too!
• Features:
• *Travel 7 Days A Week
• *Stay Your Choice Of Nights (1-4 Nights)
• *Good For Two Adults & Two Children
• *Pay Just The Taxes & Fees
• *Multiple Travel Date Requests Allowed
• *Fully Transferable To Another Person
• *Just A 30 Days Advance Notice Required
• *You Will Have 12 Months To Complete Travel After Redemption
• HOW CAN WE DO THIS?
• We contract with the world leading hotel chains and resorts to help them fill their otherwise empty rooms.
• We help fill empty rooms which the hotels, resorts and cruise lines turn into additional revenue from other areas of their property and future bookings.
• Hotels rarely experience full occupancy, yet they remain open, providing rooms and services at fixed costs. So when hotels give out their rooms by partnering with marketing companies like us, they might miss out on the room fee, but they already didn't have that in the first place, at least now they have the opportunity to gain a customer for their in-house restaurants, room service, their casinos, an extra day stay, future bookings, etc.
• VIEW ALL THE DETAILS OF THIS SPECIAL OFFER AND REDEEM ONLINE AT
• WWW.QOTAVERNIX.COM
• Certificate ID # 47261-38157
• Expires 02/29/2020
• *terms and conditions apply see website for details
• KEEP IN MIND THE EXAMPLES I AM UPLOADING ARE SIMPLY TO SHOW YOU THAT THEY CONTAIN THE "COMPLIMENTS OF" AND "EXCLUSIVELY FOR" ELEMENTS. THESE MUST BE INCLUDED IN NEW DESIGN. PLEASE ONLY USE THE CONTENT I PROVIDED IN BRIEF, DONT USE CONTENT FROM EXAMPLES.
Nice to have
• EXCITING LAS VEGAS IMAGES THAT MAKE SOMEONE WANT TO GO THERE

```html
<!DOCTYPE html>
<html lang="en">
<head>
<meta charset="utf-8">
<title>Las Vegas Vacation Getaway – Gift Voucher</title>
<link href="https://fonts.googleapis.com/css2?family=Oswald:wght@500;600;700&family=Source+Sans+3:wght@400;600;700&display=swap" rel="stylesheet">
<style>
  :root{
    --navy:#0b2f70;
    --blue:#1556b0;
    --blue-mid:#0f3f8f;
    --gold:#d9a441;
    --gold-dark:#c28d2c;
    --red:#e3211f;
    --ink:#2b2b2b;
    --grey:#e6e6e6;
    --muted:#6d6d6d;
    --white:#ffffff;
    --page:#ececec;
  }
  *{margin:0;padding:0;box-sizing:border-box}
  html,body{width:996px;height:1200px;overflow:hidden;background:var(--page)}
  body{font-family:"Source Sans 3",Arial,sans-serif;position:relative}
  .flyer{position:absolute;left:34px;top:0;width:927px;height:1200px;overflow:hidden;
    background:radial-gradient(ellipse at 40% 55%,var(--blue) 0%,var(--blue-mid) 45%,var(--navy) 100%)}
  .hero-photo{position:absolute;left:0;top:0;width:927px;height:470px;
    background:linear-gradient(160deg,#f0c46a 0%,#d9783a 22%,#7b3f8c 48%,#2b5fb8 75%,#1a3f84 100%)}
  .hero-wave{position:absolute;left:0;top:360px;width:927px;height:112px}
  .voucher-ribbon{position:absolute;left:0;top:0;width:170px;height:170px}
  .courtesy-tag{position:absolute;left:690px;top:0;width:216px;height:150px;background:var(--white);
    clip-path:polygon(0 0,100% 0,100% 100%,50% 88%,0 100%);text-align:center;padding-top:14px;
    box-shadow:0 2px 6px rgba(0,0,0,.3)}
  .courtesy-tag .tag-head{font-weight:700;color:var(--blue);font-size:16px;line-height:1.1;letter-spacing:.3px}
  .courtesy-tag .tag-brand{display:flex;align-items:center;justify-content:center;gap:6px;margin-top:8px;
    font-weight:700;font-size:17px;color:var(--blue-mid)}
  .courtesy-tag .tag-brand i{display:block;width:12px;height:12px;background:var(--red)}
  .courtesy-tag .tag-lines{font-size:10.5px;color:var(--ink);line-height:1.2;margin-top:6px}
  .snapshot{position:absolute;background:var(--white);padding:9px;box-shadow:0 4px 10px rgba(0,0,0,.35)}
  .snapshot div{width:100%;height:100%}
  .snap-gondola{left:618px;top:175px;width:300px;height:215px;transform:rotate(8deg)}
  .snap-gondola div{background:linear-gradient(170deg,#7fb4e6 0%,#e5c79a 45%,#3b6f8a 100%)}
  .snap-ride{left:519px;top:362px;width:190px;height:152px;transform:rotate(-4deg)}
  .snap-ride div{background:linear-gradient(170deg,#8cc7ee 0%,#5fb35e 55%,#e3cf4c 100%)}
  .offer-title{position:absolute;left:38px;top:458px;font-family:"Oswald",sans-serif;line-height:1}
  .offer-title .city{display:block;color:var(--gold);font-weight:600;font-size:80px;letter-spacing:.5px;text-shadow:0 2px 4px rgba(0,0,0,.35)}
  .offer-title .kind{display:block;color:var(--white);font-weight:500;font-size:43px;margin-top:2px}
  .recipients{position:absolute;left:38px;top:605px;color:var(--white);font-size:22px;line-height:33px}
  .recipients b{font-weight:700}
  .intro{position:absolute;left:38px;top:679px;width:488px;color:var(--white);font-size:15px;line-height:20.5px;text-align:justify}
  .features{position:absolute;left:554px;top:551px;width:344px;height:318px;background:var(--gold);padding:14px 18px 0 18px;color:var(--white)}
  .features h2{font-family:"Oswald",sans-serif;font-weight:600;font-size:31px;line-height:1;margin-bottom:6px}
  .features ul{list-style:none}
  .features li{display:flex;gap:10px;font-size:16.5px;line-height:22px;padding:3px 0 3px;border-bottom:1px solid rgba(255,255,255,.55)}
  .features li:last-child{border-bottom:none}
  .features li svg{flex:none;margin-top:4px}
  .details{position:absolute;left:0;top:858px;width:927px;height:270px;background:var(--grey)}
  .how-pill{position:absolute;left:0;top:833px;width:375px;height:46px;background:var(--gold);border-radius:0 23px 23px 0;
    color:var(--white);font-weight:700;font-size:23px;line-height:46px;padding-left:48px;letter-spacing:.3px}
  .how-list{position:absolute;left:48px;top:903px;width:865px;list-style:none;color:var(--ink);font-size:14.8px;line-height:21px}
  .how-list li{display:flex;gap:11px;margin-bottom:8px}
  .how-list li span{text-align:justify}
  .how-list li svg{flex:none;margin-top:3px}
  .cert-meta{position:absolute;left:0;top:1076px;width:927px;text-align:center;color:var(--muted);font-size:12.5px}
  .footer-band{position:absolute;left:0;top:1126px;width:927px;height:74px;background:var(--navy)}
  .redeem-pill{position:absolute;left:38px;top:1101px;width:863px;height:50px;background:var(--gold);border-radius:25px;
    color:var(--white);font-weight:700;font-size:18.5px;line-height:50px;text-align:center;letter-spacing:.2px}
  .redeem-pill svg{vertical-align:-2px;margin:0 6px 0 8px}
  .terms{position:absolute;left:0;top:1166px;width:927px;text-align:center;color:var(--white);font-size:13.5px}
</style>
</head>
<body>
<main class="flyer">
  <div class="hero-photo" role="img" aria-label="Smiling family of four in front of the Welcome to Fabulous Las Vegas sign"></div>

  <svg class="voucher-ribbon" viewBox="0 0 170 170">
    <polygon points="0,0 170,0 0,170" fill="var(--red)"/>
    <text x="58" y="66" transform="rotate(-45 58 66)" fill="#fff" font-family="Source Sans 3, sans-serif" font-weight="700" font-size="17" text-anchor="middle" letter-spacing="1">GIFT VOUCHER</text>
  </svg>

  <aside class="courtesy-tag">
    <p class="tag-head">THIS CERTIFICATE IS<br>COMPLIMENTS OF</p>
    <p class="tag-brand"><i></i>Pulsewire Text</p>
    <p class="tag-lines">Certificate Courtesy Of<br>Text Line 2<br>Text Line 3</p>
  </aside>

  <svg class="hero-wave" viewBox="0 0 927 112" preserveAspectRatio="none">
    <path d="M0,18 Q380,-10 927,58 L927,112 L0,112 Z" fill="#fff"/>
    <path d="M0,40 Q380,10 927,78 L927,112 L0,112 Z" fill="var(--gold)"/>
    <path d="M0,66 Q380,36 927,98 L927,112 L0,112 Z" fill="var(--blue-mid)"/>
  </svg>

  <div class="snapshot snap-gondola"><div role="img" aria-label="Couple riding a gondola along a Venetian-style canal"></div></div>
  <div class="snapshot snap-ride"><div role="img" aria-label="Children cheering on a water park ride"></div></div>

  <h1 class="offer-title"><span class="city">LAS VEGAS</span><span class="kind">VACATION GETAWAY</span></h1>

  <div class="recipients">
    <p><b>COMPLIMENTS OF:</b> Two Adults &amp; Two Children</p>
    <p><b>EXCLUSIVELY FOR:</b> Customer Name</p>
  </div>

  <p class="intro">There is no doubt that Las Vegas is one of the hottest travel destinations around the world. In fact, some people would even go as far as saying that perhaps it is THE hottest place to visit. Enjoy up to 4 nights of resort/casino accommodations in exciting Las Vegas, NV. Millions of people travel to this exciting city each year to enjoy its thrills. Thanks to the business you received this certificate from, now you can enjoy exciting Las Vegas, NV too!</p>

  <section class="features">
    <h2>FEATURES:</h2>
    <ul>
      <li><svg width="14" height="14" viewBox="0 0 14 14"><circle cx="7" cy="7" r="7" fill="#fff"/><path d="M5.5 4 L8.5 7 L5.5 10" stroke="var(--gold)" stroke-width="2" fill="none"/></svg>Travel 7 Days A Week</li>
      <li><svg width="14" height="14" viewBox="0 0 14 14"><circle cx="7" cy="7" r="7" fill="#fff"/><path d="M5.5 4 L8.5 7 L5.5 10" stroke="var(--gold)" stroke-width="2" fill="none"/></svg>Stay Your Choice Of Nights (1- 4 Nights)</li>
      <li><svg width="14" height="14" viewBox="0 0 14 14"><circle cx="7" cy="7" r="7" fill="#fff"/><path d="M5.5 4 L8.5 7 L5.5 10" stroke="var(--gold)" stroke-width="2" fill="none"/></svg>Good For Two Adults &amp; Two Children</li>
      <li><svg width="14" height="14" viewBox="0 0 14 14"><circle cx="7" cy="7" r="7" fill="#fff"/><path d="M5.5 4 L8.5 7 L5.5 10" stroke="var(--gold)" stroke-width="2" fill="none"/></svg>Pay Just The Taxes &amp; Fees</li>
      <li><svg width="14" height="14" viewBox="0 0 14 14"><circle cx="7" cy="7" r="7" fill="#fff"/><path d="M5.5 4 L8.5 7 L5.5 10" stroke="var(--gold)" stroke-width="2" fill="none"/></svg>Multiple Travel Date Requests Allowed</li>
      <li><svg width="14" height="14" viewBox="0 0 14 14"><circle cx="7" cy="7" r="7" fill="#fff"/><path d="M5.5 4 L8.5 7 L5.5 10" stroke="var(--gold)" stroke-width="2" fill="none"/></svg>Fully Transferable To Another Person</li>
      <li><svg width="14" height="14" viewBox="0 0 14 14"><circle cx="7" cy="7" r="7" fill="#fff"/><path d="M5.5 4 L8.5 7 L5.5 10" stroke="var(--gold)" stroke-width="2" fill="none"/></svg>Just A 30 Days Advance Notice Required</li>
      <li><svg width="14" height="14" viewBox="0 0 14 14"><circle cx="7" cy="7" r="7" fill="#fff"/><path d="M5.5 4 L8.5 7 L5.5 10" stroke="var(--gold)" stroke-width="2" fill="none"/></svg>You Will Have 12 Months To Complete Travel After Redemption</li>
    </ul>
  </section>

  <div class="details"></div>
  <h2 class="how-pill">HOW CAN WE DO THIS?</h2>

  <ul class="how-list">
    <li><svg width="15" height="15" viewBox="0 0 15 15"><circle cx="7.5" cy="7.5" r="6.5" fill="none" stroke="var(--gold)" stroke-width="1.6"/><path d="M6 4.8 L8.8 7.5 L6 10.2" stroke="var(--gold)" stroke-width="1.8" fill="none"/></svg><span>We contract with the world leading hotel chains and resorts to help them fill their otherwise empty rooms.</span></li>
    <li><svg width="15" height="15" viewBox="0 0 15 15"><circle cx="7.5" cy="7.5" r="6.5" fill="none" stroke="var(--gold)" stroke-width="1.6"/><path d="M6 4.8 L8.8 7.5 L6 10.2" stroke="var(--gold)" stroke-width="1.8" fill="none"/></svg><span>We help fill empty rooms which the hotels, resorts and cruise lines turn into additional revenue from other areas of their property and future bookings.</span></li>
    <li><svg width="15" height="15" viewBox="0 0 15 15"><circle cx="7.5" cy="7.5" r="6.5" fill="none" stroke="var(--gold)" stroke-width="1.6"/><path d="M6 4.8 L8.8 7.5 L6 10.2" stroke="var(--gold)" stroke-width="1.8" fill="none"/></svg><span>Hotels rarely experience full occupancy, yet they remain open, providing rooms and services at fixed costs. So when hotels give out their rooms by partnering with marketing companies like us, they might miss out on the room fee, but they already didn't have that in the first place, at least now they have the opportunity to gain a customer for their in-house restaurants, room service, their casinos, an extra day stay, future bookings, etc.</span></li>
  </ul>

  <p class="cert-meta">Certificate ID # 47261-38157 &nbsp;|&nbsp; Expires 02/29/2020</p>

  <div class="footer-band"></div>
  <p class="redeem-pill">VIEW ALL THE DETAILS OF THIS SPECIAL OFFER AND REDEEM ONLINE AT<svg width="14" height="14" viewBox="0 0 14 14"><circle cx="7" cy="7" r="6" fill="none" stroke="#fff" stroke-width="1.4"/><ellipse cx="7" cy="7" rx="2.6" ry="6" fill="none" stroke="#fff" stroke-width="1.2"/><line x1="1" y1="7" x2="13" y2="7" stroke="#fff" stroke-width="1.2"/></svg>WWW.QOTAVERNIX.COM</p>
  <p class="terms">*terms and conditions apply see website for details</p>
</main>
</body>
</html>
```